Brightfield Ventures Inc. Letterhead

Creation of attractive and eye catching letterhead for a business start-up for the construction industry. Letterhead must relate to construction, but avoid standard hammer and tools in the design.

I forgot to add some details, sorry about that. Some pertinent info: Ph: 916-555-0187 brightfieldventures.example 448 Willowmere Ave, Ste 210 Folsom, CA 95999 info@brightfieldventures.example not sure if slogan should be in there" “Connecting construction professionals to create a purpose driven industry.” must be able to be used in word. Thanks!

```html
<!DOCTYPE html>
<html lang="en">
<head>
<meta charset="utf-8">
<title>Brightfield Ventures Inc. Letterhead</title>
<link href="https://fonts.googleapis.com/css2?family=Lato:wght@400;700&family=Montserrat:wght@600&family=Yellowtail&display=block" rel="stylesheet">
<style>
  :root {
    --navy: #1c1f5c;
    --red: #c8232c;
    --body-text: #4b4b4b;
    --closing-text: #222222;
    --footer-text: #444444;
    --paper: #ffffff;
  }
  html, body {
    margin: 0;
    padding: 0;
    width: 934px;
    height: 1200px;
    overflow: hidden;
    background: var(--paper);
  }
  .letterhead {
    position: relative;
    width: 934px;
    height: 1200px;
    background: var(--paper);
    font-family: "Lato", Arial, sans-serif;
    overflow: hidden;
  }

  /* Brand lockup */
  .brand {
    position: absolute;
    top: 108px;
    left: 0;
    width: 100%;
    display: flex;
    flex-direction: column;
    align-items: center;
  }
  .brand-name-row {
    display: flex;
    align-items: center;
    gap: 10px;
  }
  .brand-mark {
    width: 14px;
    height: 14px;
    background: var(--red);
  }
  .brand-name {
    font-family: "Montserrat", Arial, sans-serif;
    font-weight: 600;
    font-size: 20px;
    letter-spacing: 1.5px;
    color: var(--navy);
    text-transform: uppercase;
    line-height: 1;
  }
  .brand-sector {
    display: flex;
    align-items: center;
    gap: 8px;
    margin-top: 6px;
    width: 206px;
  }
  .brand-sector-rule {
    flex: 1;
    height: 2px;
    background: var(--red);
  }
  .brand-sector-label {
    font-family: "Montserrat", Arial, sans-serif;
    font-weight: 600;
    font-size: 10px;
    letter-spacing: 4px;
    color: var(--red);
    text-transform: uppercase;
    line-height: 1;
  }

  /* Letter */
  .letter {
    position: absolute;
    top: 273px;
    left: 80px;
    width: 775px;
  }
  .salutation {
    margin: 0 0 18px;
    font-weight: 700;
    font-size: 16px;
    color: var(--navy);
  }
  .letter-body p {
    margin: 0 0 20px;
    font-size: 16.6px;
    line-height: 27.4px;
    color: var(--body-text);
    text-align: justify;
    hyphens: auto;
  }
  .closing {
    margin: 26px 0 0 2px;
    font-size: 19px;
    color: var(--closing-text);
  }
  .signature {
    margin: 2px 0 0 2px;
    font-family: "Yellowtail", "Brush Script MT", cursive;
    font-size: 34px;
    line-height: 1.1;
    color: var(--navy);
  }

  /* Footer */
  .footer {
    position: absolute;
    left: 108px;
    width: 720px;
    top: 1118px;
    text-align: center;
    font-size: 13px;
    color: var(--footer-text);
  }
  .footer-address,
  .footer-contacts {
    display: flex;
    justify-content: center;
    align-items: center;
    gap: 4px;
  }
  .footer-contacts { gap: 14px; }
  .footer-rule {
    height: 3px;
    background: var(--navy);
    margin: 7px 0 8px;
  }
  .contact-item {
    display: flex;
    align-items: center;
    gap: 4px;
  }
  .icon {
    width: 11px;
    height: 11px;
    fill: var(--red);
  }
</style>
</head>
<body>
<main class="letterhead">
  <header class="brand">
    <div class="brand-name-row">
      <span class="brand-mark" aria-hidden="true"></span>
      <span class="brand-name">Brightfield Ventures</span>
    </div>
    <div class="brand-sector">
      <span class="brand-sector-rule"></span>
      <span class="brand-sector-label">Construction</span>
      <span class="brand-sector-rule"></span>
    </div>
  </header>

  <section class="letter">
    <p class="salutation">Dear Mr. Lorem,</p>
    <div class="letter-body">
      <p>Lorem ipsum dolor sit amet, consectetuer adipiscing elit, sed diam nonummy nibh euismod tincidunt ut laoreet dolore magna aliquam erat volutpat. Ut wisi enim ad minim veniam, quis nostrud exerci tation ullamcorper suscipit lobortis nisl ut aliquip ex ea commodo consequat. Duis autem vel eum iriure dolor in hendiusto odio dignissim qui blandit praesent luptatum zzril delenit augue duis dolore te feugait nulla facilisi.</p>
      <p>Lorem ipsum dolor sit amet, consectetuer adipiscing elit, sed diam nonummy nibh euismod tincidunt ut laoreet dolore magna aliquam erat volutpat. Ut wisi enim ad minim veniam, quis nostrud exerci tation ullamcorper suscipit lobortis nisl ut aliquip ex ea commodo consequat. Duis autem vel eum iriure dolor in hendiusto odio dignissim qui blandit praesent luptatum zzril delenit augue duis dolore te feugait nulla facilisi.</p>
      <p>Lorem ipsum dolor sit amet, consectetuer adipiscing elit, sed diam nonummy nibh euismod tincidunt ut laoreet dolore magna aliquam erat volutpat. Ut wisi enim ad minim veniam, quis nostrud exerci tation ullamcorper suscipit lobortis nisl ut aliquip ex ea commodo consequat. Duis autem vel eum iriure dolor in hendiusto odio dignissim qui blandit praesent luptatum zzril delenit augue duis dolore te feugait nulla facilisi.</p>
    </div>
    <p class="closing">Sincerely Your,</p>
    <p class="signature">Your Name</p>
  </section>

  <footer class="footer">
    <div class="footer-address">
      <svg class="icon" viewBox="0 0 12 12" aria-hidden="true"><path d="M6 0a4.2 4.2 0 0 0-4.2 4.2C1.8 7.4 6 12 6 12s4.2-4.6 4.2-7.8A4.2 4.2 0 0 0 6 0zm0 6a1.8 1.8 0 1 1 0-3.6A1.8 1.8 0 0 1 6 6z"/></svg>
      <span>448 Willowmere Ave, Ste 210, Folsom, CA 95999</span>
    </div>
    <div class="footer-rule"></div>
    <div class="footer-contacts">
      <span class="contact-item">
        <svg class="icon" viewBox="0 0 12 12" aria-hidden="true"><path d="M2.6 0.6l1.8 2.4-1 1.3c.7 1.6 2 2.9 3.6 3.6l1.3-1 2.4 1.8-.8 2.2C5.2 10.8 1.2 6.8 0.4 1.4z"/></svg>
        Ph: 916-555-0187
      </span>
      <span class="contact-item">
        <svg class="icon" viewBox="0 0 12 12" aria-hidden="true"><path d="M0 2.5h12v7H0z M0 2.5l6 4 6-4" stroke="#fff" stroke-width="0.9"/></svg>
        info@brightfieldventures.example
      </span>
      <span class="contact-item">
        <svg class="icon" viewBox="0 0 12 12" aria-hidden="true"><circle cx="6" cy="6" r="5.6"/><path d="M0.5 6h11M6 0.5c-3 3-3 8 0 11M6 0.5c3 3 3 8 0 11" stroke="#fff" stroke-width="0.8" fill="none"/></svg>
        brightfieldventures.example
      </span>
    </div>
  </footer>
</main>
</body>
</html>
```